Leuchtkasten für Pflegedienst
Zielgruppe
Wir sind ein ambulnter Pflegedienst in Rostock. Derzeit befindet sich am Haus ein runder Leuchtkasten mit dem alten Logo. Das Logo wurde erneuert. Nun soll der Leuchtkasten mit einem Durchmessr von 80 cm neu gestaltet werden.
Aufgabenstellung
bitte zwei unterscheideliche Entwürfe für die Vorder und die Rückseite. Es sollte auf der einen Seite vielleicht das Logo anthalten sein und auf der anderen Seite eine andere kreative Idee. Hauskrankenpflege Sonnenhof Pflegehaus sollten enthalten sein, sowie die Telefonummer 0381-52846137
Auf der anderen Seite wurde ein Schriftzug in Edelstahl rostoptik montiert.
Wichtig ist, dass das der ENtwurf auf einer durchleichtbaren Folie gedruckt werden kann.
Der KAffee slogan war füe eine andere Aktion und sollte nicht auf den Leuchtkasten.

```html
<!DOCTYPE html>
<html lang="de">
<head>
<meta charset="utf-8">
<title>Leuchtkasten – Hauskrankenpflege Sonnenhof Pflegehaus</title>
<link href="https://fonts.googleapis.com/css2?family=Source+Sans+3:wght@600;700&display=swap" rel="stylesheet">
<style>
  :root {
    --page-bg: #eef0f2;
    --sign-blue: #2790d8;
    --sign-blue-deep: #1a7fcc;
    --ink-white: #ffffff;
    --icon-blue: #2790d8;
  }
  html, body {
    margin: 0;
    padding: 0;
    width: 1200px;
    height: 1200px;
    overflow: hidden;
    background: var(--page-bg);
  }
  .canvas {
    position: relative;
    width: 1200px;
    height: 1200px;
  }
  .sign-face {
    position: absolute;
    left: 110px;
    top: 110px;
    width: 980px;
    height: 980px;
    border-radius: 50%;
    background: radial-gradient(circle at 35% 30%, var(--sign-blue) 0%, var(--sign-blue) 45%, var(--sign-blue-deep) 100%);
    font-family: "Source Sans 3", "Source Sans Pro", sans-serif;
    color: var(--ink-white);
  }
  .company-name {
    position: absolute;
    left: 200px;
    top: 290px;
    margin: 0;
    font-weight: 700;
    font-size: 52px;
    line-height: 1.2;
    letter-spacing: 0.3px;
  }
  .contact-row {
    position: absolute;
    left: 150px;
    display: flex;
    align-items: center;
  }
  .contact-row--phone { top: 480px; }
  .contact-row--mail { top: 640px; }
  .contact-icon {
    width: 108px;
    height: 108px;
    border-radius: 50%;
    background: var(--ink-white);
    display: flex;
    align-items: center;
    justify-content: center;
    flex: none;
  }
  .contact-icon svg { width: 58px; height: 58px; }
  .phone-number {
    margin-left: 48px;
    font-weight: 700;
    font-size: 76px;
    letter-spacing: 1px;
  }
  .mail-address {
    margin-left: 48px;
    font-weight: 700;
    font-size: 36px;
    letter-spacing: 0.3px;
  }
</style>
</head>
<body>
  <div class="canvas">
    <div class="sign-face">
      <h1 class="company-name">Hauskrankenpflege<br>Sonnenhof Pflegehaus</h1>

      <div class="contact-row contact-row--phone">
        <div class="contact-icon">
          <svg viewBox="0 0 24 24" aria-hidden="true">
            <path fill="var(--icon-blue)" d="M6.6 10.8c1.4 2.8 3.8 5.1 6.6 6.6l2.2-2.2c.3-.3.7-.4 1-.2 1.1.4 2.3.6 3.6.6.6 0 1 .4 1 1V20c0 .6-.4 1-1 1C10.6 21 3 13.4 3 4c0-.6.4-1 1-1h3.5c.6 0 1 .4 1 1 0 1.3.2 2.5.6 3.6.1.3 0 .7-.2 1l-2.3 2.2z"/>
          </svg>
        </div>
        <span class="phone-number">0381-52846137</span>
      </div>

      <div class="contact-row contact-row--mail">
        <div class="contact-icon">
          <svg viewBox="0 0 24 24" aria-hidden="true">
            <rect x="2.5" y="5" width="19" height="14" rx="1" fill="none" stroke="var(--icon-blue)" stroke-width="1.8"/>
            <polyline points="2.5,5.5 12,13 21.5,5.5" fill="none" stroke="var(--icon-blue)" stroke-width="1.8" stroke-linejoin="round"/>
            <polyline points="2.5,18.5 9.5,11.5 M14.5,11.5 21.5,18.5" fill="none" stroke="var(--icon-blue)" stroke-width="1.6"/>
            <line x1="14.5" y1="11.5" x2="21.5" y2="18.5" stroke="var(--icon-blue)" stroke-width="1.6"/>
          </svg>
        </div>
        <span class="mail-address">info@sonnenhof-pflegehaus.de</span>
      </div>
    </div>
  </div>
</body>
</html>
```